Tour operator needs simple coded WordPress site (updated extra payment for coding and guaranteed)

[update 9/7/2015]
If you design a new logo and it gets accepted, even if we use another template with your logo you will get $50
[update 8/7/2015]
Update on questions about dual-language
For dual languages we are happy to set up a second site with the same designs in a second language.
For the design aspect just allow the user to switch between languages with an icon.
For the coding, a replica of the site on a second server will do (to save messing around with multiple language plugins) - we will populate it with Chinese text
[original post]
Simple coded WordPress site for tours
You can choose to design only or design and code ($340 design, $150 bonus for coding)
Open design brief - use your creativity
Will be in 2 languages (English and Chinese) but design needs only to be in one language
Winning design will be chosen only from home page, but the winner must make a second standard template page when chosen at no extra cost.
Must be responsive design
We only need homepage and standard template page design and coding, we will populate the pages
You can use design ideas from our pamphlet if you like - attached
Only a sample logo and colors on website and pamphlet - feel free to change as the current ones seem restrictive
Current website framework only to give an idea of the number of pages and basic menu structure (no need to use existing navigation style or any style at all for that matter, open brief)
http://brightwattlejourneys.com.au/
Target Market(s)
Chinese parents of kids 10-14 (the kids will take the tour)
Industry/Entity Type
Tour
Number of Pages Required
2 page
Look and feel
Each slider illustrates characteristics of the customer's brand and the style your logo design should communicate.

```html
<!DOCTYPE html>
<html lang="en">
<head>
<meta charset="utf-8">
<title>Southern Horizon Exchange</title>
<link rel="stylesheet" href="https://fonts.googleapis.com/css2?family=Ubuntu:wght@400;500;700&family=Oswald:wght@500&display=swap">
<style>
:root{
  --navy:#2f3e80;
  --gold:#f4b21b;
  --ink:#2a2a2a;
  --text:#3a3a3a;
  --white:#ffffff;
  --dark:#262626;
}
*{margin:0;padding:0;box-sizing:border-box}
html,body{width:1200px;height:1048px;overflow:hidden;background:var(--white)}
body{position:relative;font-family:"Ubuntu",sans-serif;color:var(--text)}
.lang-switch{position:absolute;left:159px;top:23px;width:119px;height:35px;background:var(--dark);border-radius:4px;color:var(--white);font-size:13px;display:flex;align-items:center;padding-left:18px;gap:7px}
.lang-switch .flag{width:20px;height:13px;background:#3b4a8f;border:1px solid #cfd3e6}
.book-now{position:absolute;left:950px;top:21px;width:89px;height:33px;background:var(--gold);color:var(--white);font-size:14px;font-weight:500;display:flex;align-items:center;justify-content:center;border-radius:2px}
.brand{position:absolute;left:478px;top:14px;width:245px;height:118px;background:var(--white);border-radius:0 0 6px 6px;display:flex;flex-direction:column;align-items:center;justify-content:flex-end;padding-bottom:8px;gap:12px;z-index:3}
.brand .dot{width:62px;height:62px;border-radius:50%;background:var(--gold)}
.brand .name{font-size:15px;font-weight:500;color:var(--navy);white-space:nowrap}
.main-nav{position:absolute;left:0;top:95px;width:1200px;height:42px;background:var(--navy)}
.main-nav a{position:absolute;top:0;height:42px;display:flex;align-items:center;justify-content:center;color:var(--white);font-size:15px;font-weight:500;text-decoration:none;border-right:1px solid rgba(255,255,255,.18)}
.main-nav a.first{border-left:1px solid rgba(255,255,255,.18)}
.main-nav a.active{box-shadow:inset 0 -4px 0 var(--gold)}
.hero{position:absolute;left:0;top:137px;width:1200px;height:420px;background:linear-gradient(180deg,#b9c9d9 0%,#8ea3b6 40%,#8a5a4d 70%,#6d2f2c 100%)}
.hero .arrow{position:absolute;top:208px}
.hero-caption{position:absolute;left:159px;top:266px;background:rgba(0,0,0,.45);border-left:4px solid var(--gold);padding:9px 14px 10px 13px;font-family:"Oswald",sans-serif;font-weight:500;font-size:28px;line-height:34px;color:var(--white);letter-spacing:-.6px}
.feature{position:absolute;top:524px;width:300px;text-align:center}
.feature .badge{width:144px;height:144px;margin:0 auto;border-radius:50%;background:var(--white);display:flex;align-items:center;justify-content:center}
.feature h3{margin-top:3px;font-size:16px;line-height:20px;font-weight:500;color:var(--ink);white-space:nowrap}
.feature.current h3{color:var(--navy)}
.rule{position:absolute;left:130px;top:719px;width:940px;height:2px;background:linear-gradient(90deg,rgba(0,0,0,0),#cfcfcf 20%,#cfcfcf 80%,rgba(0,0,0,0))}
.about{position:absolute;left:0;top:722px;width:1200px;height:284px;background:linear-gradient(180deg,#fff 0%,#f4f4f4 100%);text-align:center}
.about h2{margin-top:44px;font-size:27px;font-weight:500;color:var(--navy)}
.about h2 .gold{color:var(--gold)}
.about .divider{position:relative;margin:8px auto 0;width:640px;height:20px}
.about .divider::before{content:"";position:absolute;left:0;right:0;top:9px;height:1px;background:#cfcfcf}
.about .divider span{position:absolute;left:310px;top:0;width:20px;height:20px;border-radius:50%;background:var(--navy);border:4px solid var(--gold)}
.about .lead{margin:14px auto 0;width:860px;font-size:13.4px;font-weight:500;line-height:18px;color:var(--ink)}
.about .body{margin:12px auto 0;width:840px;font-size:13.6px;line-height:18px;color:#444}
.read-more{display:inline-block;margin-top:17px;width:106px;height:33px;line-height:33px;background:var(--dark);color:var(--white);font-size:14px;font-weight:500;border-radius:3px}
.site-footer{position:absolute;left:0;top:1006px;width:1200px;height:42px;background:var(--navy);color:var(--white);font-size:12.5px}
.site-footer p{position:absolute;left:161px;top:14px}
.social{position:absolute;top:2px;width:39px;height:39px;border-radius:50%;background:#dfe3ee;border:3px solid var(--white)}
</style>
</head>
<body>
<div class="lang-switch"><span class="flag"></span>English
<svg width="10" height="7" viewBox="0 0 10 7"><path d="M1 1l4 4 4-4" fill="none" stroke="#fff" stroke-width="1.6"/></svg></div>
<div class="brand"><span class="dot"></span><span class="name">SOUTHERN HORIZON EXCHANGE</span></div>
<a class="book-now">Book Now</a>

<nav class="main-nav">
  <a class="first active" style="left:159px;width:141px">HOME</a>
  <a style="left:300px;width:149px">TOURS</a>
  <a class="first" style="left:750px;width:156px">CONTACT</a>
  <a style="left:906px;width:132px">ABOUT</a>
</nav>

<section class="hero" role="img" aria-label="Photo of smiling students walking along a river boardwalk with a steel bridge behind them">
  <svg class="arrow" style="left:106px" width="18" height="30" viewBox="0 0 18 30"><path d="M15 2L3 15l12 13" fill="none" stroke="#fff" stroke-width="3"/></svg>
  <svg class="arrow" style="left:1076px" width="18" height="30" viewBox="0 0 18 30"><path d="M3 2l12 13L3 28" fill="none" stroke="#fff" stroke-width="3"/></svg>
  <div class="hero-caption">EDUCATIONAL, SAFE, CULTURALLY SOUTHERN<br>HORIZON EXCHANGE ENLIGHTENING AND FUN.</div>
</section>

<div class="feature current" style="left:122px">
  <div class="badge"><svg width="124" height="124" viewBox="0 0 124 124">
    <circle cx="62" cy="62" r="60" fill="none" stroke="#2f3e80" stroke-width="2"/>
    <circle cx="62" cy="62" r="55" fill="#2f3e80"/>
    <path d="M62 38l30 13-30 13-30-13z" fill="#fff"/>
    <path d="M44 58v12c0 5 36 5 36 0V58l-18 8z" fill="#fff"/>
    <rect x="38" y="78" width="40" height="10" rx="5" fill="none" stroke="#fff" stroke-width="2.5"/>
  </svg></div>
  <h3>Educational And Cultural</h3>
</div>

<div class="feature" style="left:448px">
  <div class="badge"><svg width="124" height="124" viewBox="0 0 124 124">
    <circle cx="62" cy="62" r="60" fill="none" stroke="#f4b21b" stroke-width="2"/>
    <circle cx="62" cy="62" r="55" fill="#f4b21b"/>
    <path d="M62 32l26 9v18c0 18-12 29-26 35-14-6-26-17-26-35V41z" fill="#fff"/>
    <path d="M48 62l10 10 18-20" fill="none" stroke="#f4b21b" stroke-width="7"/>
  </svg></div>
  <h3>Safe And Secure</h3>
</div>

<div class="feature" style="left:775px">
  <div class="badge"><svg width="124" height="124" viewBox="0 0 124 124">
    <circle cx="62" cy="62" r="60" fill="none" stroke="#f4b21b" stroke-width="2"/>
    <circle cx="62" cy="62" r="55" fill="#f4b21b"/>
    <g fill="none" stroke="#fff" stroke-width="3">
      <circle cx="66" cy="62" r="24"/>
      <ellipse cx="66" cy="62" rx="10" ry="24"/>
      <path d="M42 62h48M46 50h40M46 74h40"/>
    </g>
    <path d="M28 58l22-4 8-14h4l-3 14 10 2-10 4 3 12h-4l-8-12z" fill="#fff"/>
  </svg></div>
  <h3>Travel insurance</h3>
</div>

<div class="rule"></div>

<section class="about">
  <h2><span class="gold">ABOUT</span> SOUTHERN <span class="gold">HORIZON</span> EXCHANGE</h2>
  <div class="divider"><span></span></div>
  <p class="lead">At The Southern Horizon Exchange We Are Passionate About Educational Travel And Opportunities For Students To Gain Academic And Cultural Understanding Of Australia.</p>
  <p class="body">14 day premium cultural and educational tours to Australian cities. Educational, safe, culturally enlightening and fun. Learn about educational institutions, history, sports, laws and customs, food and culture while improving your English.</p>
  <a class="read-more">READ MORE</a>
</section>

<footer class="site-footer">
  <p>© 2015&nbsp; SOUTHERN HORIZON EXCHANGE. All Rights Reserved.</p>
  <span class="social" style="left:907px" aria-label="Social link"></span>
  <span class="social" style="left:953px" aria-label="Social link"></span>
  <span class="social" style="left:999px" aria-label="Social link"></span>
</footer>
</body>
</html>
```